Business card for Luxury Portable Restroom Trailer company

We are a Luxury Portable Restroom Trailer Company Called FALCRIDGE HIRES. Based in Orange County California. We provide portable restroom trailers for events, such as, Weddings, Concerts, Charity events, Sporting events, Tournaments, Corporate events, ect. We rent and Sell the Luxury restrooms. Our colors are white, grey, and Orange. As you will see in the logo we uploaded.
There are 2 people in the company so the names and titles will change for the 3 people but card will remain the same. Here is the information for each Person: Dwight Penner CFO 555 318-0476
next Person: Leon Marchetti VP 555 318-0476
Next Person: Owen Marchetti CEO 555 318-0476
Information to include on the card: Luxury Restroom Trailers Rental and Sales. Weddings, Concerts, Charity, Sporting and Corp. Events.

```html
<!DOCTYPE html>
<html lang="en">
<head>
<meta charset="utf-8">
<title>Falcridge Hires – Business Card</title>
<link href="https://fonts.googleapis.com/css2?family=Montserrat:wght@400;500;700;800&display=swap" rel="stylesheet">
<style>
  :root {
    --orange: #f26f23;
    --grey: #58595b;
    --white: #ffffff;
    --backdrop: #e9e9ea;
    --ink: #2e2e30;
  }
  * { box-sizing: border-box; margin: 0; padding: 0; }
  html, body { width: 1200px; height: 880px; overflow: hidden; }
  body {
    background: var(--backdrop);
    font-family: "Montserrat", Arial, sans-serif;
    position: relative;
  }
  .card {
    position: absolute;
    left: 260px;
    width: 680px;
    height: 388px;
    background: var(--white);
    overflow: hidden;
    box-shadow: 0 6px 18px rgba(0,0,0,0.18);
  }
  .card--front { top: 36px; }
  .card--back { top: 456px; }

  /* Front */
  .brand-frame {
    position: absolute;
    left: 110px; top: 78px;
    width: 460px; height: 140px;
    border: 5px solid var(--grey);
    display: flex; align-items: center; justify-content: center;
  }
  .brand-name {
    font-weight: 800;
    font-size: 44px;
    letter-spacing: 2px;
    color: var(--grey);
    white-space: nowrap;
  }
  .services {
    position: absolute;
    left: 0; right: 0; top: 262px;
    text-align: center;
    font-size: 17px;
    font-weight: 500;
    color: var(--ink);
    line-height: 1.75;
  }
  .services .dot {
    display: inline-block;
    width: 9px; height: 9px;
    border-radius: 50%;
    background: var(--orange);
    margin: 0 8px 2px 10px;
    vertical-align: middle;
  }

  /* Back */
  .back-panel {
    position: absolute;
    left: 0; top: 0; bottom: 0;
    width: 440px;
    background: var(--orange);
  }
  .back-brand {
    position: absolute;
    left: 36px; top: 34px;
    padding: 10px 16px;
    border: 3px solid var(--white);
  }
  .back-brand .brand-name {
    color: var(--white);
    font-size: 22px;
    letter-spacing: 1px;
  }
  .team {
    position: absolute;
    left: 56px; top: 108px;
    color: var(--white);
    list-style: none;
  }
  .member { margin-bottom: 12px; }
  .member__name {
    font-weight: 700;
    font-size: 21px;
    letter-spacing: 0.5px;
    text-transform: uppercase;
    line-height: 1.15;
  }
  .member__title {
    font-size: 15px;
    font-weight: 400;
    margin-left: 18px;
    line-height: 1.3;
  }
  .member__phone {
    font-size: 15px;
    margin-left: 38px;
    display: flex; align-items: center; gap: 8px;
    line-height: 1.3;
  }
  .member__phone svg { width: 15px; height: 15px; fill: var(--white); }
  .emblem {
    position: absolute;
    left: 370px; top: 22px;
    width: 344px; height: 344px;
    border-radius: 50%;
    background: var(--white);
    display: flex; align-items: center; justify-content: center;
  }
  .emblem__ring {
    width: 316px; height: 316px;
    border-radius: 50%;
    border: 12px solid var(--orange);
    display: flex; align-items: center; justify-content: center;
    text-align: center;
  }
  .emblem .brand-name {
    color: var(--orange);
    font-size: 30px;
    white-space: normal;
    line-height: 1.15;
  }
</style>
</head>
<body>
  <section class="card card--front" aria-label="Card front">
    <div class="brand-frame"><span class="brand-name">FALCRIDGE HIRES</span></div>
    <p class="services">
      <span class="dot"></span>Luxury Restroom Trailers Rental and Sales<br>
      <span class="dot"></span>Weddings<span class="dot"></span>Concerts<span class="dot"></span>Charity<span class="dot"></span>Sporting and Corp<span class="dot"></span>Events
    </p>
  </section>

  <section class="card card--back" aria-label="Card back">
    <div class="back-panel"></div>
    <div class="back-brand"><span class="brand-name">FALCRIDGE HIRES</span></div>
    <ul class="team">
      <li class="member">
        <div class="member__name">Dwight Penner</div>
        <div class="member__title">CFO</div>
        <div class="member__phone"><svg viewBox="0 0 24 24" aria-hidden="true"><path d="M6.6 10.8c1.4 2.8 3.8 5.1 6.6 6.6l2.2-2.2c.3-.3.7-.4 1-.2 1.1.4 2.3.6 3.6.6.6 0 1 .4 1 1V20c0 .6-.4 1-1 1C10.6 21 3 13.4 3 4c0-.6.4-1 1-1h3.5c.6 0 1 .4 1 1 0 1.3.2 2.5.6 3.6.1.3 0 .7-.2 1l-2.3 2.2z"/></svg>555 318-0476</div>
      </li>
      <li class="member">
        <div class="member__name">Leon Marchetti</div>
        <div class="member__title">VP</div>
        <div class="member__phone"><svg viewBox="0 0 24 24" aria-hidden="true"><path d="M6.6 10.8c1.4 2.8 3.8 5.1 6.6 6.6l2.2-2.2c.3-.3.7-.4 1-.2 1.1.4 2.3.6 3.6.6.6 0 1 .4 1 1V20c0 .6-.4 1-1 1C10.6 21 3 13.4 3 4c0-.6.4-1 1-1h3.5c.6 0 1 .4 1 1 0 1.3.2 2.5.6 3.6.1.3 0 .7-.2 1l-2.3 2.2z"/></svg>555 318-0476</div>
      </li>
      <li class="member">
        <div class="member__name">Owen Marchetti</div>
        <div class="member__title">CEO</div>
        <div class="member__phone"><svg viewBox="0 0 24 24" aria-hidden="true"><path d="M6.6 10.8c1.4 2.8 3.8 5.1 6.6 6.6l2.2-2.2c.3-.3.7-.4 1-.2 1.1.4 2.3.6 3.6.6.6 0 1 .4 1 1V20c0 .6-.4 1-1 1C10.6 21 3 13.4 3 4c0-.6.4-1 1-1h3.5c.6 0 1 .4 1 1 0 1.3.2 2.5.6 3.6.1.3 0 .7-.2 1l-2.3 2.2z"/></svg>555 318-0476</div>
      </li>
    </ul>
    <div class="emblem">
      <div class="emblem__ring"><span class="brand-name">FALCRIDGE<br>HIRES</span></div>
    </div>
  </section>
</body>
</html>
```